Brackwell Exteriors Needs a New Website!

We are an exteriors company specializing in vinyl siding, Corwin Maddox siding, aluminum soffit/fascia, trough. We do new construction work as well as renovations. We also build detached garages.
You can view our current website at www.brackwellfabricators.ca
I want to completely overhaul the website.
Our services are different now as we no longer do new home construction as well as we do not do the snow clearing.
I want to focus on 2 things in particular on the website:

1/ Exterior renovations

2/ Detached Garage construction.

I have included our logo in the attached files to use as well.

Some features we would like:

1/ Be able to easily attach a video from Clipverse/Reelio to highlight a product or service
2/ Quick chat or contact button that we can talk to a potential client quickly
3/ Meet the Team page that is interesting and fresh
4/ Place for us to put in helpful exterior tips/suggestions for homeowners.

Content is not important, but looking for the best design that will attract people once they click on our page and want to renovate with us.

Target Market(s)

People looking for renovations on their home, people looking to build a detached garage.

Industry/Entity Type

Residential Construction

Number of Pages Required

5+ page

Font styles to use
Sans Serif

Requirements
Must have
• Fresh and exciting home page.

Simple design. Don't want it over complicated or too much information to confuse the potential client.

Easy way to contact us.

Meet the team page that instills confidence
Nice to have
• Colour of website to go off our logo. Doesn't need to be an exact match, but something that goes well with our blue and grey.

```html
<!DOCTYPE html>
<html lang="en">
<head>
<meta charset="utf-8">
<title>Brackwell Exteriors</title>
<link href="https://fonts.googleapis.com/css2?family=Montserrat:wght@400;500;600;700&family=Roboto:wght@400;500&display=swap" rel="stylesheet">
<style>
:root{
  --blue:#1b5fbd;
  --blue-deep:#154f9f;
  --blue-title:#1d63c2;
  --ink:#222;
  --muted:#6d6d6d;
  --line:#d9d9d9;
  --soft:#f3f3f3;
  --dark:#1e1e1e;
  --white:#fff;
}
*{margin:0;padding:0;box-sizing:border-box}
html,body{width:1200px;height:4662px;overflow:hidden}
body{font-family:"Roboto",sans-serif;color:var(--ink);background:var(--white);position:relative}
.abs{position:absolute}
.section-title{position:absolute;left:0;width:1200px;text-align:center;font-family:"Montserrat",sans-serif;font-weight:500;font-size:30px;color:var(--blue-title);letter-spacing:.5px}
.section-sub{position:absolute;left:0;width:1200px;text-align:center;font-family:"Montserrat",sans-serif;font-size:16.5px;color:#333}
.on-blue .section-title,.on-blue .section-sub{color:var(--white)}

/* header */
.site-header{position:absolute;top:0;left:0;width:1200px;height:121px;background:var(--white)}
.brand{position:absolute;left:112px;top:36px;display:flex;align-items:center;gap:12px}
.brand-dot{width:46px;height:46px;border-radius:50%;background:var(--blue)}
.brand-name{font-family:"Montserrat",sans-serif;font-weight:700;font-size:24px;color:var(--blue)}
.nav{position:absolute;top:52px;font-family:"Montserrat",sans-serif;font-size:12.5px;font-weight:500;color:#333}
.nav.active{color:var(--blue)}
.quote-btn{position:absolute;left:901px;top:36px;width:187px;height:50px;border-radius:25px;background:var(--blue);color:var(--white);font-family:"Montserrat",sans-serif;font-size:12.5px;font-weight:600;display:flex;align-items:center;justify-content:center}

/* hero */
.hero{position:absolute;top:121px;left:0;width:1200px;height:729px;background:linear-gradient(180deg,#0f2850 0%,#1d3e6a 35%,#5a5342 65%,#3a4a2a 90%)}
.hero-kicker{position:absolute;top:348px;left:0;width:1200px;text-align:center;font-family:"Montserrat",sans-serif;font-size:28px;color:var(--white);letter-spacing:1px}
.hero-title{position:absolute;top:395px;left:0;width:1200px;text-align:center;font-family:"Montserrat",sans-serif;font-weight:600;font-size:50px;color:var(--white);letter-spacing:1px}
.play{position:absolute;left:551px;top:471px;width:98px;height:98px}
.hero-curve{position:absolute;left:0;bottom:0;width:1200px;height:729px}

/* services */
.service-card{position:absolute;top:1019px;width:308px;height:529px;background:var(--white);border:1px solid #e0e0e0;box-shadow:0 2px 8px rgba(0,0,0,.12)}
.service-photo{height:235px;width:100%}
.service-name{position:absolute;top:262px;left:0;width:100%;height:56px;display:flex;align-items:center;justify-content:center;text-align:center;font-family:"Montserrat",sans-serif;font-size:16px;font-weight:500;line-height:24px;color:#222}
.service-text{position:absolute;top:324px;left:18px;right:18px;text-align:center;font-size:12.5px;line-height:26px;color:var(--muted)}
.read-more{position:absolute;top:455px;left:81px;width:146px;height:48px;border:1.5px solid var(--blue);border-radius:24px;color:var(--blue);font-family:"Montserrat",sans-serif;font-weight:600;font-size:13px;display:flex;align-items:center;justify-content:center}

/* featured */
.featured{position:absolute;top:1620px;left:0;width:1200px;height:592px;background:var(--blue)}
.work-tile{position:absolute;top:177px;width:234px;height:337px;border:1px solid rgba(255,255,255,.5)}
.work-caption{position:absolute;left:0;bottom:0;height:44px;padding:0 10px;display:flex;align-items:center;background:rgba(0,0,0,.55);color:var(--white);font-family:"Montserrat",sans-serif;font-size:11px;font-weight:500}
.dot{position:absolute;top:551px;width:12px;height:12px;border-radius:50%;background:var(--white)}
.dot.on{background:#111}

/* why us */
.why{position:absolute;top:2212px;left:0;width:1200px;height:711px;background:var(--soft)}
.perk-icon{position:absolute;width:100px;height:100px}
.perk-title{position:absolute;font-family:"Montserrat",sans-serif;font-size:18.5px;font-weight:500;color:#222}
.perk-text{position:absolute;width:330px;font-size:12.5px;line-height:25px;color:var(--muted)}

/* team */
.member-photo{position:absolute;top:3090px;width:312px;height:230px}
.member-card{position:absolute;top:3289px;width:278px;height:156px;background:var(--white);border:1px solid #e3e3e3;text-align:center}
.member-name{margin-top:27px;font-family:"Montserrat",sans-serif;font-weight:600;font-size:15.5px;color:#222}
.member-role{margin-top:9px;font-size:12.5px;color:var(--muted)}
.member-social{margin-top:14px;display:flex;justify-content:center;gap:9px}
.member-social span{width:40px;height:40px;border-radius:50%;border:1px solid #cfcfcf}
.team-arrow{position:absolute;top:3245px;width:24px;height:96px}

/* faq */
.faq-photo{position:absolute;top:3512px;left:615px;width:585px;height:582px;background:linear-gradient(160deg,#c9b79a 0%,#a98d6b 45%,#8c7559 100%)}
.faq-title{position:absolute;top:3600px;left:110px;font-family:"Montserrat",sans-serif;font-weight:600;font-size:30px;color:var(--blue-title)}
.faq-sub{position:absolute;top:3652px;left:113px;font-family:"Montserrat",sans-serif;font-size:16.5px;color:#333}
.faq-item{position:absolute;left:112px;width:458px;background:var(--white);border:1px solid #d6d6d6}
.faq-q{height:49px;display:flex;align-items:center;padding:0 14px;font-family:"Montserrat",sans-serif;font-size:15.5px;color:#333}
.faq-q b{font-weight:700;font-size:20px;margin-right:8px;color:#222}
.faq-q svg{margin-left:auto}
.faq-a{padding:4px 48px 0 48px;font-size:11.5px;line-height:24px;color:var(--muted)}

/* contact */
.contact{position:absolute;top:4094px;left:0;width:1200px;height:489px;background:var(--blue)}
.field{position:absolute;background:var(--white);border-radius:3px;font-family:"Times New Roman",serif;font-size:13.5px;color:#333;padding:15px 17px}
.submit{position:absolute;left:525px;top:368px;width:148px;height:54px;border:1.5px solid var(--white);border-radius:27px;color:var(--white);font-family:"Montserrat",sans-serif;font-size:16px;font-weight:500;display:flex;align-items:center;justify-content:center}

/* footer */
.site-footer{position:absolute;top:4583px;left:0;width:1200px;height:79px;background:var(--dark)}
.copyright{position:absolute;top:31px;left:0;width:1200px;text-align:center;font-size:11.5px;color:#ddd}
.live-chat{position:absolute;left:858px;top:29px;width:206px;height:50px;background:var(--blue);color:var(--white);font-family:"Montserrat",sans-serif;font-size:16px;font-weight:500;display:flex;align-items:center;justify-content:center;gap:9px}
</style>
</head>
<body>

<header class="site-header">
  <div class="brand"><span class="brand-dot"></span><span class="brand-name">Brackwell Exteriors</span></div>
  <span class="nav active" style="left:434px">HOME</span>
  <span class="nav" style="left:516px">OUR SERVICES</span>
  <span class="nav" style="left:655px">MEET THE TEAM</span>
  <span class="nav" style="left:803px">CONTACT US</span>
  <span class="quote-btn">REQUEST A QUOTE</span>
</header>

<section class="hero" role="img" aria-label="Large lit two-storey home at dusk with lawn and trees">
  <div class="hero-kicker">EXPERIENCE THE</div>
  <div class="hero-title">BRACKWELL DIFFERENCE</div>
  <svg class="play" viewBox="0 0 98 98"><circle cx="49" cy="49" r="46" fill="#1b5fbd" stroke="#fff" stroke-width="4"/><path d="M38 30 L68 49 L38 68Z" fill="#fff"/></svg>
  <svg class="hero-curve" viewBox="0 0 1200 729" preserveAspectRatio="none">
    <path d="M0 628 Q600 796 1200 628 L1200 729 L0 729Z" fill="#1b5fbd"/>
    <path d="M0 640 Q600 808 1200 640 L1200 729 L0 729Z" fill="#fff"/>
  </svg>
</section>

<section class="services">
  <h2 class="section-title" style="top:903px">OUR SERVICES</h2>
  <p class="section-sub" style="top:957px">Brackwell Builders is a homebuilder with quality craftsmanship &amp; unwavering integrity.</p>

  <article class="service-card" style="left:112px">
    <div class="service-photo" role="img" aria-label="House exterior under renovation with scaffolding" style="background:linear-gradient(180deg,#a9c7e8,#7a6a58 70%,#5b4a3a)"></div>
    <h3 class="service-name">EXTERIOR RENOVATIONS</h3>
    <p class="service-text">Brackwell Builders is a homebuilder with quality craftsmanship &amp; unwavering integrity. Today, our commitment to quality shows in every we do, from our exceptional</p>
    <span class="read-more">READ MORE</span>
  </article>
  <article class="service-card" style="left:446px">
    <div class="service-photo" role="img" aria-label="Detached stone garage with black iron fence" style="background:linear-gradient(180deg,#a7c0d6,#8e7e70 55%,#3c4a35)"></div>
    <h3 class="service-name">DETACHED GARAGE<br>CONSTRUCTION</h3>
    <p class="service-text">Brackwell's exterior division is Edmonton's exterior finishing experts. Completing the exteriors on several hundred homes a year will be done right and on budget.</p>
    <span class="read-more">READ MORE</span>
  </article>
  <article class="service-card" style="left:780px">
    <div class="service-photo" role="img" aria-label="Large new home with stone and siding exterior" style="background:linear-gradient(180deg,#b7c6d3,#6b5d52 60%,#4a4540)"></div>
    <h3 class="service-name">OTHER SERVICES</h3>
    <p class="service-text">Looking for a reputable company to replace those aging shingles? Wanting to update the look of your home to add more curb appeal? We can handle all your exterior</p>
    <span class="read-more">READ MORE</span>
  </article>
</section>

<section class="featured on-blue">
  <h2 class="section-title" style="top:57px">FEATURED WORK</h2>
  <p class="section-sub" style="top:111px">Brackwell Builders is a homebuilder with quality craftsmanship &amp; unwavering integrity.</p>
  <div class="work-tile" style="left:112px;background:linear-gradient(180deg,#2a3a55,#5a4a3a 65%,#3a2e24)" role="img" aria-label="Modern home lit at dusk"><span class="work-caption">AWARD WINNING EXTERIORS</span></div>
  <div class="work-tile" style="left:359px;background:linear-gradient(160deg,#7a5a40,#a27a55 50%,#4a3a2c)" role="img" aria-label="Wooden staircase framing in a new build"><span class="work-caption">CUSTOM HOME CONSTRUCTION</span></div>
  <div class="work-tile" style="left:606px;background:linear-gradient(180deg,#b8bec6,#3a3d44 55%,#cfd3d8)" role="img" aria-label="Dark-sided house in winter snow"><span class="work-caption">UNRIVALLED QUALITY</span></div>
  <div class="work-tile" style="left:854px;background:linear-gradient(180deg,#e2e0dc,#9a9792 60%,#6d6a66)" role="img" aria-label="Bright kitchen with grey cabinets"><span class="work-caption">TURNING DREAMS INTO REALITY</span></div>
  <span class="dot" style="left:575px"></span>
  <span class="dot on" style="left:594px"></span>
  <span class="dot" style="left:612px"></span>
</section>

<section class="why">
  <h2 class="section-title" style="top:50px">WHY US?</h2>
  <p class="section-sub" style="top:104px">Brackwell Builders is a homebuilder with quality craftsmanship</p>

  <svg class="perk-icon" style="left:111px;top:206px" viewBox="0 0 100 100" fill="none" stroke="#1b5fbd" stroke-width="2"><circle cx="50" cy="50" r="48"/><circle cx="50" cy="42" r="7"/><path d="M36 66c2-10 26-10 28 0"/><path d="M50 22l2 4 4 .5-3 3 .8 4-3.8-2-3.8 2 .8-4-3-3 4-.5z"/><circle cx="31" cy="50" r="5"/><circle cx="69" cy="50" r="5"/></svg>
  <h3 class="perk-title" style="left:241px;top:210px">Certified Experience</h3>
  <p class="perk-text" style="left:237px;top:246px">Having professionals do the job gives you the confiden the job will be done right, on budget, and on time.</p>

  <svg class="perk-icon" style="left:643px;top:206px" viewBox="0 0 100 100" fill="none" stroke="#1b5fbd" stroke-width="2"><circle cx="50" cy="50" r="48"/><path d="M32 48h8v22h-8z"/><path d="M40 50l8-14c3-4 7-2 6 3l-2 8h12c3 0 4 3 3 5l-4 14c-1 2-2 3-4 3H40"/></svg>
  <h3 class="perk-title" style="left:773px;top:210px">Guaranteed Satisfaction</h3>
  <p class="perk-text" style="left:769px;top:246px">We aren't happy unless you are. Along with a robust limited lifetime warranty on our work</p>

  <svg class="perk-icon" style="left:111px;top:360px" viewBox="0 0 100 100" fill="none" stroke="#1b5fbd" stroke-width="2"><circle cx="50" cy="50" r="48"/><path d="M28 32h44v28H46l-10 9v-9h-8z"/><circle cx="40" cy="46" r="2"/><circle cx="50" cy="46" r="2"/><circle cx="60" cy="46" r="2"/></svg>
  <h3 class="perk-title" style="left:241px;top:364px">Superior Communication</h3>
  <p class="perk-text" style="left:237px;top:400px">Taking the time to explain the construction process and promptly answering the phone or email</p>

  <svg class="perk-icon" style="left:643px;top:360px" viewBox="0 0 100 100" fill="none" stroke="#1b5fbd" stroke-width="2"><circle cx="50" cy="50" r="48"/><path d="M30 34h22l20 20-18 18-20-20z"/><circle cx="39" cy="43" r="3"/></svg>
  <h3 class="perk-title" style="left:773px;top:364px">Competitive Pricing</h3>
  <p class="perk-text" style="left:769px;top:400px">Although we offer the best in services, we won't blow your budget on the job.</p>

  <svg class="perk-icon" style="left:111px;top:529px" viewBox="0 0 100 100" fill="none" stroke="#1b5fbd" stroke-width="2"><circle cx="50" cy="50" r="48"/><path d="M50 26l20 7v14c0 13-9 21-20 26-11-5-20-13-20-26V33z"/><rect x="43" y="48" width="14" height="11"/><path d="M46 48v-4a4 4 0 018 0v4"/></svg>
  <h3 class="perk-title" style="left:241px;top:533px">Safety Conscience</h3>
  <p class="perk-text" style="left:237px;top:569px">COR certification, liability insurance, and WCB coverage on all workers gives you peace of mind</p>

  <svg class="perk-icon" style="left:643px;top:529px" viewBox="0 0 100 100" fill="none" stroke="#1b5fbd" stroke-width="2"><circle cx="50" cy="50" r="48"/><circle cx="50" cy="42" r="13"/><circle cx="50" cy="42" r="7"/><path d="M41 52l-8 18 7-2 3 6 7-14M59 52l8 18-7-2-3 6-7-14"/></svg>
  <h3 class="perk-title" style="left:773px;top:533px">Unrivalled Quality</h3>
  <p class="perk-text" style="left:769px;top:569px">Our greatest asset is our unrivalled pursuit of a "top of the line" job each and every time.</p>
</section>

<section class="team">
  <h2 class="section-title" style="top:2980px">MEET THE TEAM</h2>
  <p class="section-sub" style="top:3034px">Brackwell Builders is a homebuilder with quality craftsmanship</p>

  <svg class="team-arrow" style="left:62px" viewBox="0 0 24 96" fill="none" stroke="#888" stroke-width="1.5"><path d="M20 2 L4 48 L20 94"/></svg>
  <svg class="team-arrow" style="left:1125px" viewBox="0 0 24 96" fill="none" stroke="#888" stroke-width="1.5"><path d="M4 2 L20 48 L4 94"/></svg>

  <div class="member-photo" style="left:112px;background:linear-gradient(180deg,#9aa36a,#7d8a4d 60%,#6b7a8e)" role="img" aria-label="Portrait of the general manager in a field of tall grass"></div>
  <div class="member-photo" style="left:445px;background:linear-gradient(180deg,#a3a56e,#84884f 60%,#5e5a52)" role="img" aria-label="Portrait of the renovations manager in a field of tall grass"></div>
  <div class="member-photo" style="left:777px;background:linear-gradient(180deg,#9ea46a,#7f874c 60%,#3e3b3a)" role="img" aria-label="Portrait of the administrative assistant in a field of tall grass"></div>

  <div class="member-card" style="left:129px">
    <div class="member-name">DORIAN KESSLER</div>
    <div class="member-role">General Manager</div>
    <div class="member-social"><span></span><span></span></div>
  </div>
  <div class="member-card" style="left:462px">
    <div class="member-name">MARCUS TILDEN</div>
    <div class="member-role">Renovations Manager</div>
    <div class="member-social"><span></span><span></span></div>
  </div>
  <div class="member-card" style="left:794px">
    <div class="member-name">ELENA VAUGHN</div>
    <div class="member-role">Administrative Assistant</div>
    <div class="member-social"><span></span><span></span></div>
  </div>
</section>

<section class="faq">
  <div class="faq-photo" role="img" aria-label="Family sitting under a cardboard roof holding a potted plant"></div>
  <h2 class="faq-title">FAQ'S</h2>
  <p class="faq-sub">Brackwell's exterior division is Edmonton's exterior...</p>

  <div class="faq-item" style="top:3712px"><div class="faq-q"><b>Q.</b>Sed ut perspiciatis unde omnis iste natus?<svg width="12" height="8" viewBox="0 0 12 8"><path d="M1 1l5 5 5-5" fill="none" stroke="#555" stroke-width="1.5"/></svg></div></div>
  <div class="faq-item" style="top:3770px;height:125px"><div class="faq-q"><b>Q.</b>Sed ut perspiciatis unde omnis iste natus?<svg width="12" height="8" viewBox="0 0 12 8"><path d="M1 1l5 5 5-5" fill="none" stroke="#555" stroke-width="1.5"/></svg></div><p class="faq-a">Nemo enim ipsam voluptatem quia voluptas sit aspernatur aut odit aut fugit, sed quia consequuntur magni dolores...</p></div>
  <div class="faq-item" style="top:3908px"><div class="faq-q"><b>Q.</b>Sed ut perspiciatis unde omnis iste natus?<svg width="12" height="8" viewBox="0 0 12 8"><path d="M1 1l5 5 5-5" fill="none" stroke="#555" stroke-width="1.5"/></svg></div></div>
  <div class="faq-item" style="top:3969px"><div class="faq-q"><b>Q.</b>Sed ut perspiciatis unde omnis iste natus?<svg width="12" height="8" viewBox="0 0 12 8"><path d="M1 1l5 5 5-5" fill="none" stroke="#555" stroke-width="1.5"/></svg></div></div>
</section>

<section class="contact on-blue">
  <h2 class="section-title" style="top:42px">CONTACT US</h2>
  <p class="section-sub" style="top:96px">Brackwell Builders is a homebuilder with quality craftsmanship</p>
  <div class="field" style="left:261px;top:158px;width:333px;height:47px">First Name :</div>
  <div class="field" style="left:605px;top:158px;width:333px;height:47px">Last Name :</div>
  <div class="field" style="left:261px;top:219px;width:333px;height:47px">Email :</div>
  <div class="field" style="left:605px;top:219px;width:333px;height:47px">Phone :</div>
  <div class="field" style="left:261px;top:279px;width:677px;height:65px">Message :</div>
  <span class="submit">SUBMIT</span>
</section>

<footer class="site-footer">
  <p class="copyright">© Copyrights 2020 Brackwell Builders.All Rights Reserved.</p>
  <span class="live-chat"><svg width="20" height="16" viewBox="0 0 20 16" fill="none" stroke="#fff" stroke-width="1.6"><path d="M2 2h11v8H6l-3 3v-3H2z"/><path d="M15 5h3v7h-1v2l-2-2h-5"/></svg>LIVE CHAT</span>
</footer>

</body>
</html>
```